Lotstallmart.com Webpage Design

Design Brief for lotstallmart.com (Copy of Brief also in attached Word file)

Name of Website- lotstallmart.com (existing logo and look & feel of website to be changed)

Logo - Finalised. The logo files are attached with the brief as “logo.jpeg”. The “Blue- Grey” version of the logo is for use on lighter backgrounds and the “Orange-White” version of the logo is for use on darker backgrounds. (A full Black version of the logo is also attached). Both versions may be used in different parts of the website. All attached files are in .png format.
Status - The website in functional and is undergoing user trials. However, we want to improve the look & feel of the website so at it seems
a. cotemporary,
b. Easy to Navigate
c. professional and
d. Vibrant.

Please visit ‘lotstallmart.com’ to check out the website and its functionalities – please use it only as a reference for the features & functions to be provided, however the designer should use a ‘Free Hand’ in designing the composition of various parts of the webpage without getting too influenced by the existing design

Objective of the Website ‘lotstallmart.com –
a. It is a portal focussed on listing of ‘Retail’ specific real-estate properties by developers, owners and realty brokers. The properties shall listed under the following four categories-
i. Retail Malls
ii. Shopping Complexes
iii. High-street shops
iv. Retail Warehouses
*refer lotstallmart.com for better clarity

b. The abovementioned properties shall be listed either for ‘Sale’ or ‘rent\lease’ or both

c. Users shall visit the site in case they wish to acquire a retail \ shop space either on ‘sale’ or ‘rent’. These Users would be able to specify the ‘Search Criteria’ through the tool-bars provided on the website – the ‘Search Criteria’ shall comprise of ‘Type of space category’, ‘City’, ‘Locality’, transaction type ie ‘Rent \ Sale’ and ‘Area Range’

d. The main revenue model for the website shall be listing fee ( or advertising charges ) payable by those listing their properties on the website.

Three Main Pages of Website (lotstallmart.com) that need to be designed -
a. Main Home Page (visit the web link - http://lotstallmart.com/ ) - The main home page has the “Search Toolbar” for specifying of Search Criteria by the User. It shall also have the following features & functions-
i. Main Advertising Banner
ii. Featured Projects
iii. New Launches
iv. Toolbar with buttons – ‘Advertise with Us’, ‘Listings Alert’, ‘Mart Wizards’, ‘Advertiser Login’

b. Property Listings Page (visit the web link - http://lotstallmart.com/gurgaon-in-india ) - The List of property options that match the Criteria specified by the ‘User’ get displayed on this page.

c. Property Detail Page - When the ‘User’ clicks on the “More….” Button on the ‘Property Listings Page’ (given in point b. above) the web page with the details of the property opens. (For Example – visit the web link - http://lotstallmart.com/vorne-Shopping-Complex-vorne-quadrion-gurgaon-636 )

Note:- Please refer to attached ‘Shopping’ related images the designer may use them on the website to provide a look & feel of retail if required – either separately or rotate in a single window

Target Market(s)

Retailers & Investors looking for retail space, Real Estate Brokers, Developers

Industry/Entity Type

Advertising

Number of Pages Required

3 page

Requirements
Must have
• Refer to existing site lotstallmart.com -- all the existing functionalities are a must have.
Nice to have
• The Designer may use the retail related images on the website if required for making it more vibrant. Refer attached images Shopping(1-6).jpg

```html
<!DOCTYPE html>
<html lang="en">
<head>
<meta charset="utf-8">
<title>Lotstallmart.com – Retail Space Portal</title>
<link href="https://fonts.googleapis.com/css2?family=Ubuntu:wght@400;500;700&family=Open+Sans:wght@400;600;700&display=swap" rel="stylesheet">
<style>
:root{
  --orange:#f1aa3c;
  --orange-dark:#d98f22;
  --sand:#f3c27a;
  --cream:#fcf5ea;
  --charcoal:#2d2d2d;
  --ink:#1f1f1f;
  --grey:#8a8a8a;
  --grey-light:#b9b9b9;
  --white:#ffffff;
}
*{box-sizing:border-box;margin:0;padding:0}
html,body{width:1200px;height:2609px;overflow:hidden}
body{font-family:"Open Sans",Arial,sans-serif;color:var(--ink);background:var(--cream)}
.wrap{width:800px;margin:0 auto;position:relative}

/* top bar */
.topbar{height:70px;background:var(--charcoal);color:var(--white)}
.topbar .wrap{height:70px}
.brand{position:absolute;left:0;top:18px;display:flex;align-items:center;gap:9px}
.brand-dot{width:24px;height:24px;border-radius:50%;background:var(--orange)}
.brand-name{font-family:"Ubuntu",sans-serif;font-weight:700;font-size:22px;color:var(--white)}
.hotline{position:absolute;left:504px;top:12px;font-size:12px;color:#cfcfcf}
.hotline svg{vertical-align:-2px;margin-right:4px}
.hotline strong{display:block;font-size:16px;color:var(--white);font-weight:600;margin-top:4px}
.social{position:absolute;left:668px;top:10px;display:flex;gap:14px}
.social span{width:14px;height:14px;border-radius:3px;background:#dcdcdc;display:block}
.account{position:absolute;right:0;top:42px;display:flex;gap:16px;font-size:11px}
.account svg{vertical-align:-2px;margin-right:4px}

/* nav */
.mainnav{height:34px;background:var(--orange)}
.mainnav ul{list-style:none;display:flex;margin-left:-9px;width:818px;height:34px}
.mainnav li{font-size:11.5px;font-weight:600;text-transform:uppercase;color:var(--ink);display:flex;align-items:center;justify-content:center;border-right:1px solid var(--orange-dark);padding:0 20px;flex:1 1 auto}
.mainnav li:first-child{flex:0 0 70px;padding:0;background:var(--charcoal);color:var(--white)}
.mainnav li:last-child{border-right:none}

/* hero */
.hero{height:348px;position:relative;background:linear-gradient(90deg,#8a5a2e 0%,#c79a63 30%,#e3c79b 55%,#b98652 75%,#e9dcc5 100%)}
.search-title{position:absolute;left:496px;top:58px;width:208px;height:35px;background:var(--orange);font-family:"Ubuntu",sans-serif;font-weight:700;font-size:21px;display:flex;align-items:center;justify-content:center;color:var(--ink)}
.search-panel{position:absolute;left:287px;top:105px;width:617px;height:191px;background:rgba(20,20,20,.82);padding:18px 23px}
.search-grid{display:grid;grid-template-columns:212px 205px 157px;column-gap:0;row-gap:18px}
.field label{display:block;color:var(--white);font-size:11.5px;margin-bottom:6px}
.field .select{width:157px;height:27px;background:var(--white);font-size:11px;color:var(--grey-light);display:flex;align-items:center;justify-content:space-between;padding:0 8px}
.field .select::after{content:"";border:4px solid transparent;border-top-color:#555;margin-top:4px}
.search-btn{align-self:end;width:164px;height:28px;background:var(--orange);border-radius:3px;color:var(--white);font-size:11px;font-weight:600;display:flex;align-items:center;justify-content:center;text-transform:uppercase}

/* promo band */
.promo{height:108px;background:var(--sand)}
.promo .wrap{display:flex;padding-top:15px}
.promo-item{display:flex;align-items:center;gap:14px;width:279px}
.promo-icon{width:78px;height:78px;border-radius:50%;background:#a87a3a;display:flex;align-items:center;justify-content:center}
.promo-item p{font-size:12px;color:var(--ink);margin-bottom:8px}
.promo-btn{display:inline-block;background:#f8d9a2;border-radius:4px;padding:4px 10px;font-family:"Ubuntu",sans-serif;font-weight:500;font-size:15px;color:var(--ink)}

/* sections */
.featured{height:466px;background:var(--cream);padding-top:28px}
.launches{height:866px;background:var(--sand);padding-top:42px}
.news{height:438px;background:var(--cream);padding-top:38px}
.section-head{display:flex;justify-content:space-between;align-items:center;border-bottom:2px dotted #555;padding-bottom:4px}
.section-head h2{font-family:"Ubuntu",sans-serif;font-weight:500;font-size:21px}
.arrows{display:flex;gap:5px;margin-right:-2px}
.arrows span{width:18px;height:18px;border-radius:2px;background:#6b6b6b;display:flex;align-items:center;justify-content:center}
.news .section-head{border:none}
.news .section-head h2{border-bottom:2px dotted #555;width:800px;padding-bottom:4px}

.cards{display:flex;gap:44px;margin-top:22px}
.launches .cards{margin-top:24px}
.launches .cards + .cards{margin-top:46px}
.card{width:238px;position:relative}
.photo{height:140px;display:block}
.photo.house-blue{background:linear-gradient(180deg,#3f8fd8 0%,#9fc6e6 35%,#8c9db0 55%,#5f9b3a 80%,#4b7d2a 100%)}
.photo.house-pool{background:linear-gradient(180deg,#2f78c8 0%,#f0e3c8 35%,#e8d6b2 70%,#3aa7d8 85%,#2c8ec0 100%)}
.photo.house-stone{background:linear-gradient(180deg,#6aa0d8 0%,#4e7a3a 30%,#7a6a58 55%,#93806a 75%,#5a8a3a 100%)}
.photo.news-photo{height:123px;background:linear-gradient(135deg,#6f8a3e 0%,#b7a986 45%,#7a6f66 70%,#3c3a36 100%)}
.badge{position:absolute;top:-13px;right:-6px;width:44px;height:44px;border-radius:50%;display:flex;align-items:center;justify-content:center;font-family:"Ubuntu",sans-serif;font-weight:700;font-size:14px}
.badge.sale{background:var(--charcoal);color:var(--white)}
.badge.rent{background:var(--white);color:var(--ink);border:2px solid var(--charcoal)}
.card h3{font-family:"Ubuntu",sans-serif;font-weight:500;font-size:18px;margin-top:10px;padding-bottom:7px;border-bottom:1px dotted #777}
.meta{display:flex;justify-content:space-between;align-items:center;margin-top:9px}
.meta .loc{font-size:11.5px;color:var(--grey);display:flex;align-items:center;gap:6px}
.meta .price{font-size:15px;font-weight:600}
.date{font-size:11.5px;font-weight:600;margin:8px 0 10px}
.card p{font-size:11.5px;line-height:16px;color:var(--grey);margin-top:12px;height:64px}
.launches .card p{color:#8a6a3a}
.news .card p{margin-top:15px}
.btn{display:inline-block;margin-top:10px;padding:5px 9px;border-radius:3px;font-size:11px;font-weight:600;color:var(--white)}
.btn.light{background:var(--orange)}
.btn.dark{background:var(--charcoal)}

/* footer */
.footer{height:226px;background:#333;color:var(--white)}
.footer .wrap{display:flex;padding-top:30px}
.footer h4{font-family:"Ubuntu",sans-serif;font-weight:500;font-size:16px;color:var(--orange);margin-bottom:12px}
.col-about{width:207px;font-size:11.5px;line-height:20px}
.col-about p{width:140px}
.col-follow{width:252px}
.col-links{width:171px;font-size:11.5px}
.col-links li{list-style:none;margin-bottom:9px}
.col-contact{font-size:11.5px}
.col-contact li{list-style:none;display:flex;gap:14px;margin-bottom:12px;line-height:20px}
.follow-icons{display:flex;gap:10px;margin-bottom:20px}
.follow-icons span{width:24px;height:24px;border-radius:3px;background:#8a8a8a;display:block}
.follow-icons span:nth-child(2){background:var(--orange)}
.email-box{width:184px;height:26px;background:var(--white);color:var(--grey-light);font-size:11px;padding:0 6px;display:flex;align-items:center}
.subscribe{display:inline-block;margin:12px 0 0 102px;background:var(--orange);padding:4px 9px;border-radius:3px;font-size:11px;font-weight:600}
.col-about .btn{margin:6px 0 0 65px}
.copyright{height:53px;background:var(--orange);font-size:11px;color:#5a4020;display:flex;align-items:center;justify-content:center}
</style>
</head>
<body>

<header class="topbar">
  <div class="wrap">
    <div class="brand"><span class="brand-dot"></span><span class="brand-name">lotstallmart</span></div>
    <div class="hotline">
      <svg width="11" height="11" viewBox="0 0 24 24"><path fill="#cfcfcf" d="M6.6 10.8a15 15 0 0 0 6.6 6.6l2.2-2.2c.3-.3.7-.4 1-.2 1.1.4 2.3.6 3.6.6.6 0 1 .4 1 1V20c0 .6-.4 1-1 1A17 17 0 0 1 3 4c0-.6.4-1 1-1h3.5c.6 0 1 .4 1 1 0 1.3.2 2.5.6 3.6.1.3 0 .7-.2 1z"/></svg>Free Line For Us
      <strong>+123-555-0142</strong>
    </div>
    <div class="social"><span></span><span></span><span></span><span></span><span></span></div>
    <div class="account">
      <span><svg width="10" height="10" viewBox="0 0 10 10"><circle cx="5" cy="3" r="2.5" fill="#fff"/><path d="M0 10a5 4 0 0 1 10 0z" fill="#fff"/></svg>Login</span>
      <span><svg width="10" height="10" viewBox="0 0 10 10"><path d="M1 1h5v8H1z" fill="none" stroke="#fff"/><path d="M4 5h6M8 3l2 2-2 2" stroke="#fff" fill="none"/></svg>Register</span>
    </div>
  </div>
</header>

<nav class="mainnav">
  <div class="wrap">
    <ul>
      <li>Home</li><li>About Us</li><li>Property Listing</li><li>Property Details</li><li>Advertise With Us</li><li>Contact Us</li>
    </ul>
  </div>
</nav>

<section class="hero" role="img" aria-label="Interior of a bright retail space with wooden cabinets and large windows">
  <div class="search-title">Search Your House</div>
  <div class="search-panel">
    <div class="search-grid">
      <div class="field"><label>Type of space</label><div class="select">Retail Malls</div></div>
      <div class="field"><label>City</label><div class="select">Gurgaon</div></div>
      <div class="field"><label>Locality</label><div class="select">Gurgaon</div></div>
      <div class="field"><label>Transaction Type</label><div class="select">Rent</div></div>
      <div class="field"><label>Area Range(sq ft)</label><div class="select">15,000</div></div>
      <div class="search-btn">Search Your Property</div>
    </div>
  </div>
</section>

<section class="promo">
  <div class="wrap">
    <div class="promo-item">
      <div class="promo-icon"><svg width="38" height="38" viewBox="0 0 24 24"><path d="M3 10v4h3l6 4V6L6 10z" fill="#fff"/><path d="M15 9c1.5 1.5 1.5 4.5 0 6M18 7c2.6 2.6 2.6 7.4 0 10" stroke="#fff" stroke-width="1.6" fill="none"/></svg></div>
      <div><p>Sell your property easily....!</p><span class="promo-btn">Advertise with Us »</span></div>
    </div>
    <div class="promo-item">
      <div class="promo-icon"><svg width="38" height="38" viewBox="0 0 24 24"><circle cx="12" cy="13" r="7.5" fill="none" stroke="#fff" stroke-width="2"/><path d="M12 9v4l3 2" stroke="#fff" stroke-width="2" fill="none"/><path d="M4 5l3-2M20 5l-3-2" stroke="#fff" stroke-width="2"/></svg></div>
      <div><p>Get our latest updates....!</p><span class="promo-btn">Listing Alert »</span></div>
    </div>
    <div class="promo-item">
      <div class="promo-icon"><svg width="38" height="38" viewBox="0 0 24 24"><circle cx="9" cy="9" r="3.5" fill="#fff"/><path d="M2 21a7 6 0 0 1 14 0z" fill="#fff"/><circle cx="18" cy="6" r="4" fill="none" stroke="#fff" stroke-width="1.5"/><path d="M18 4v3M18 8.5v.5" stroke="#fff" stroke-width="1.5"/></svg></div>
      <div><p>Follow our expert advices..!</p><span class="promo-btn">Mart Wizards »</span></div>
    </div>
  </div>
</section>

<section class="featured">
  <div class="wrap">
    <div class="section-head"><h2>Featured Properties</h2>
      <div class="arrows"><span><svg width="8" height="8" viewBox="0 0 8 8"><path d="M6 0v8L1 4z" fill="#fff"/></svg></span><span><svg width="8" height="8" viewBox="0 0 8 8"><path d="M2 0v8l5-4z" fill="#fff"/></svg></span></div>
    </div>
    <div class="cards">
      <article class="card"><div class="photo house-blue" role="img" aria-label="Two-storey suburban house with lawn"></div><h3>Vela 81 High Street</h3><div class="meta"><span class="loc"><svg width="10" height="13" viewBox="0 0 10 13"><path d="M5 0a4.5 4.5 0 0 1 4.5 4.5C9.5 8 5 13 5 13S.5 8 .5 4.5A4.5 4.5 0 0 1 5 0z" fill="#999"/><circle cx="5" cy="4.5" r="1.7" fill="#fcf5ea"/></svg>Surat,Sector-81</span><span class="price">$ 250000</span></div><p>Lorem Ipsum is simply dummy text of the printing and typesetting industry. Lorem Ipsum has been the industry's standard dummy text ever since the 1500s...</p><span class="btn light">Read More</span></article>
      <article class="card"><div class="photo house-pool" role="img" aria-label="White villa with swimming pool"></div><h3>Vela 81 High Street</h3><div class="meta"><span class="loc"><svg width="10" height="13" viewBox="0 0 10 13"><path d="M5 0a4.5 4.5 0 0 1 4.5 4.5C9.5 8 5 13 5 13S.5 8 .5 4.5A4.5 4.5 0 0 1 5 0z" fill="#999"/><circle cx="5" cy="4.5" r="1.7" fill="#fcf5ea"/></svg>Surat,Sector-81</span><span class="price">$ 250000</span></div><p>Lorem Ipsum is simply dummy text of the printing and typesetting industry. Lorem Ipsum has been the industry's standard dummy text ever since the 1500s...</p><span class="btn light">Read More</span></article>
      <article class="card"><div class="photo house-stone" role="img" aria-label="Stone family house among trees"></div><h3>Vela 81 High Street</h3><div class="meta"><span class="loc"><svg width="10" height="13" viewBox="0 0 10 13"><path d="M5 0a4.5 4.5 0 0 1 4.5 4.5C9.5 8 5 13 5 13S.5 8 .5 4.5A4.5 4.5 0 0 1 5 0z" fill="#999"/><circle cx="5" cy="4.5" r="1.7" fill="#fcf5ea"/></svg>Surat,Sector-81</span><span class="price">$ 250000</span></div><p>Lorem Ipsum is simply dummy text of the printing and typesetting industry. Lorem Ipsum has been the industry's standard dummy text ever since the 1500s...</p><span class="btn light">Read More</span></article>
    </div>
  </div>
</section>

<section class="launches">
  <div class="wrap">
    <div class="section-head"><h2>New Launches</h2>
      <div class="arrows"><span><svg width="8" height="8" viewBox="0 0 8 8"><path d="M6 0v8L1 4z" fill="#fff"/></svg></span><span><svg width="8" height="8" viewBox="0 0 8 8"><path d="M2 0v8l5-4z" fill="#fff"/></svg></span></div>
    </div>
    <div class="cards">
      <article class="card"><div class="photo house-blue" role="img" aria-label="Two-storey suburban house with lawn"></div><span class="badge sale">Sale</span><h3>Vela 81 High Street</h3><div class="meta"><span class="loc"><svg width="10" height="13" viewBox="0 0 10 13"><path d="M5 0a4.5 4.5 0 0 1 4.5 4.5C9.5 8 5 13 5 13S.5 8 .5 4.5A4.5 4.5 0 0 1 5 0z" fill="#8a6a3a"/><circle cx="5" cy="4.5" r="1.7" fill="#f3c27a"/></svg>Surat,Sector-81</span><span class="price">$ 250000</span></div><p>Lorem Ipsum is simply dummy text of the printing and typesetting industry. Lorem Ipsum has been the industry's standard dummy text ever since the 1500s...</p><span class="btn dark">Read More</span></article>
      <article class="card"><div class="photo house-pool" role="img" aria-label="White villa with swimming pool"></div><span class="badge sale">Sale</span><h3>Vela 81 High Street</h3><div class="meta"><span class="loc"><svg width="10" height="13" viewBox="0 0 10 13"><path d="M5 0a4.5 4.5 0 0 1 4.5 4.5C9.5 8 5 13 5 13S.5 8 .5 4.5A4.5 4.5 0 0 1 5 0z" fill="#8a6a3a"/><circle cx="5" cy="4.5" r="1.7" fill="#f3c27a"/></svg>Surat,Sector-81</span><span class="price">$ 250000</span></div><p>Lorem Ipsum is simply dummy text of the printing and typesetting industry. Lorem Ipsum has been the industry's standard dummy text ever since the 1500s...</p><span class="btn dark">Read More</span></article>
      <article class="card"><div class="photo house-stone" role="img" aria-label="Stone family house among trees"></div><span class="badge rent">Rent</span><h3>Vela 81 High Street</h3><div class="meta"><span class="loc"><svg width="10" height="13" viewBox="0 0 10 13"><path d="M5 0a4.5 4.5 0 0 1 4.5 4.5C9.5 8 5 13 5 13S.5 8 .5 4.5A4.5 4.5 0 0 1 5 0z" fill="#8a6a3a"/><circle cx="5" cy="4.5" r="1.7" fill="#f3c27a"/></svg>Surat,Sector-81</span><span class="price">$ 250000</span></div><p>Lorem Ipsum is simply dummy text of the printing and typesetting industry. Lorem Ipsum has been the industry's standard dummy text ever since the 1500s...</p><span class="btn dark">Read More</span></article>
    </div>
    <div class="cards">
      <article class="card"><div class="photo house-blue" role="img" aria-label="Two-storey suburban house with lawn"></div><span class="badge sale">Sale</span><h3>Vela 81 High Street</h3><div class="meta"><span class="loc"><svg width="10" height="13" viewBox="0 0 10 13"><path d="M5 0a4.5 4.5 0 0 1 4.5 4.5C9.5 8 5 13 5 13S.5 8 .5 4.5A4.5 4.5 0 0 1 5 0z" fill="#8a6a3a"/><circle cx="5" cy="4.5" r="1.7" fill="#f3c27a"/></svg>Surat,Sector-81</span><span class="price">$ 250000</span></div><p>Lorem Ipsum is simply dummy text of the printing and typesetting industry. Lorem Ipsum has been the industry's standard dummy text ever since the 1500s...</p><span class="btn dark">Read More</span></article>
      <article class="card"><div class="photo house-pool" role="img" aria-label="White villa with swimming pool"></div><span class="badge rent">Rent</span><h3>Vela 81 High Street</h3><div class="meta"><span class="loc"><svg width="10" height="13" viewBox="0 0 10 13"><path d="M5 0a4.5 4.5 0 0 1 4.5 4.5C9.5 8 5 13 5 13S.5 8 .5 4.5A4.5 4.5 0 0 1 5 0z" fill="#8a6a3a"/><circle cx="5" cy="4.5" r="1.7" fill="#f3c27a"/></svg>Surat,Sector-81</span><span class="price">$ 250000</span></div><p>Lorem Ipsum is simply dummy text of the printing and typesetting industry. Lorem Ipsum has been the industry's standard dummy text ever since the 1500s...</p><span class="btn dark">Read More</span></article>
      <article class="card"><div class="photo house-stone" role="img" aria-label="Stone family house among trees"></div><span class="badge rent">Rent</span><h3>Vela 81 High Street</h3><div class="meta"><span class="loc"><svg width="10" height="13" viewBox="0 0 10 13"><path d="M5 0a4.5 4.5 0 0 1 4.5 4.5C9.5 8 5 13 5 13S.5 8 .5 4.5A4.5 4.5 0 0 1 5 0z" fill="#8a6a3a"/><circle cx="5" cy="4.5" r="1.7" fill="#f3c27a"/></svg>Surat,Sector-81</span><span class="price">$ 250000</span></div><p>Lorem Ipsum is simply dummy text of the printing and typesetting industry. Lorem Ipsum has been the industry's standard dummy text ever since the 1500s...</p><span class="btn dark">Read More</span></article>
    </div>
  </div>
</section>

<section class="news">
  <div class="wrap">
    <div class="section-head"><h2>Latest News</h2></div>
    <div class="cards">
      <article class="card"><h3>De Finibus Bonorum</h3><div class="date">January 12,2015</div><div class="photo news-photo" role="img" aria-label="Senior couple reading news together"></div><p>Lorem Ipsum is simply dummy text of the printing and typesetting industry. Lorem Ipsum has been the industry's standard dummy text ever since the 1500s..</p><span class="btn light">Read More</span></article>
      <article class="card"><h3>De Finibus Bonorum</h3><div class="date">January 12,2015</div><div class="photo news-photo" role="img" aria-label="Senior couple reading news together"></div><p>Lorem Ipsum is simply dummy text of the printing and typesetting industry. Lorem Ipsum has been the industry's standard dummy text ever since the 1500s..</p><span class="btn light">Read More</span></article>
      <article class="card"><h3>De Finibus Bonorum</h3><div class="date">January 12,2015</div><div class="photo news-photo" role="img" aria-label="Senior couple reading news together"></div><p>Lorem Ipsum is simply dummy text of the printing and typesetting industry. Lorem Ipsum has been the industry's standard dummy text ever since the 1500s..</p><span class="btn light">Read More</span></article>
    </div>
  </div>
</section>

<footer class="footer">
  <div class="wrap">
    <div class="col-about">
      <h4>About Us</h4>
      <p>Lotstallmart.com is a Specialised Web based platform for Retail Space, featuring properties across India under various</p>
      <span class="btn light">Read More</span>
    </div>
    <div class="col-follow">
      <h4>Follow Us On</h4>
      <div class="follow-icons"><span></span><span></span><span></span><span></span></div>
      <h4>Newsletter Signup</h4>
      <div class="email-box">Your Email</div>
      <span class="subscribe">SUBSCRIBE</span>
    </div>
    <div class="col-links">
      <h4>Quick Links</h4>
      <ul><li>Home</li><li>About Us</li><li>Property Listing</li><li>Property Details</li><li>Advertise With Us</li><li>Contact Us</li></ul>
    </div>
    <div class="col-contact">
      <h4>Contact Us</h4>
      <ul>
        <li><svg width="10" height="13" viewBox="0 0 10 13"><path d="M5 0a4.5 4.5 0 0 1 4.5 4.5C9.5 8 5 13 5 13S.5 8 .5 4.5A4.5 4.5 0 0 1 5 0z" fill="#fff"/><circle cx="5" cy="4.5" r="1.7" fill="#333"/></svg><span>Lorem Ipsum is simply<br>dummy text of the print-</span></li>
        <li><svg width="12" height="12" viewBox="0 0 24 24"><path fill="#fff" d="M6.6 10.8a15 15 0 0 0 6.6 6.6l2.2-2.2c.3-.3.7-.4 1-.2 1.1.4 2.3.6 3.6.6.6 0 1 .4 1 1V20c0 .6-.4 1-1 1A17 17 0 0 1 3 4c0-.6.4-1 1-1h3.5c.6 0 1 .4 1 1 0 1.3.2 2.5.6 3.6.1.3 0 .7-.2 1z"/></svg><span>+91-123-555-0142</span></li>
        <li><svg width="13" height="10" viewBox="0 0 13 10"><rect x=".5" y=".5" width="12" height="9" fill="none" stroke="#fff"/><path d="M.5.5l6 5 6-5" fill="none" stroke="#fff"/></svg><span>www.lotstallmart.com</span></li>
      </ul>
    </div>
  </div>
</footer>
<div class="copyright">All Rights Reserved@ 2014www.lotstallmart.com</div>

</body>
</html>
```